TWPC Business Card Design

Business card for sole operator professional civil and traffic engineer.
Clients are developers and planners who require assistance with traffic strategic master planning advice and design development for access and infrastructure associated with the development.
Colours already in use are greens for the business name and black for other legend. The attached file shows the letterhead template which is currently in use.
Target Market(s)
Professional Clients in development industry
Most clients known to the Principal and card is mostly required to allow ongoing contact
Industry/Entity Type
Business
Contact Information for Business Card
LACHLAN PETTIGREW CONSULTING PARTNERS
ABN 37 814 529 106
PO Box 418 KELWOOD NSW 2619
Lachlan Pettigrew 0412 358 971
l.pettigrew@corvanmail.net

```html
<!DOCTYPE html>
<html lang="en">
<head>
<meta charset="utf-8">
<title>TWPC Business Card</title>
<link rel="stylesheet" href="https://fonts.googleapis.com/css2?family=Cinzel:wght@500&family=Arimo:wght@400&display=swap">
<style>
  :root {
    --page-bg: #ececec;
    --card-white: #ffffff;
    --band-black: #050505;
    --accent-green: #9ccb3b;
    --text-black: #111111;
    --text-white: #ffffff;
  }
  html, body {
    margin: 0;
    padding: 0;
    width: 1200px;
    height: 864px;
    overflow: hidden;
    background: var(--page-bg);
  }
  .business-card {
    position: absolute;
    left: 150px;
    top: 157px;
    width: 900px;
    height: 550px;
    background: var(--card-white);
    box-shadow: 0 10px 30px rgba(0, 0, 0, 0.12);
    overflow: hidden;
  }
  .card-shapes {
    position: absolute;
    inset: 0;
  }
  .band-black { fill: var(--band-black); }
  .band-green { fill: var(--accent-green); }
  .company-name {
    position: absolute;
    left: 58px;
    top: 158px;
    margin: 0;
    font-family: "Cinzel", "Trajan Pro", serif;
    font-weight: 500;
    font-size: 29px;
    letter-spacing: 0.6px;
    color: var(--text-black);
    white-space: nowrap;
  }
  .principal-name {
    position: absolute;
    left: 632px;
    top: 296px;
    margin: 0;
    font-family: "Arimo", Arial, sans-serif;
    font-size: 27px;
    font-weight: 400;
    color: var(--text-black);
    white-space: nowrap;
  }
  .contact-list {
    position: absolute;
    left: 56px;
    top: 244px;
    margin: 0;
    padding: 0;
    list-style: none;
    font-family: "Arimo", Arial, sans-serif;
    font-size: 23px;
    color: var(--text-white);
  }
  .contact-item {
    display: flex;
    align-items: center;
    height: 38px;
    white-space: nowrap;
  }
  .contact-icon {
    width: 22px;
    height: 22px;
    margin-right: 24px;
    fill: var(--accent-green);
    flex: none;
  }
</style>
</head>
<body>
  <article class="business-card">
    <svg class="card-shapes" width="900" height="550" viewBox="0 0 900 550" aria-hidden="true">
      <polygon class="band-black" points="0,216 500,216 688,452 0,452"/>
      <polygon class="band-green" points="520,200 900,200 900,426 700,426"/>
    </svg>

    <h1 class="company-name">Lachlan Pettigrew Consulting Partners</h1>
    <p class="principal-name">Lachlan Pettigrew</p>

    <ul class="contact-list">
      <li class="contact-item">
        <svg class="contact-icon" viewBox="0 0 24 24" aria-hidden="true">
          <path d="M3 7c0-2 3-4 9-4s9 2 9 4v2h-5V7H8v2H3z"/>
          <path d="M6 11h12l2 9H4z"/>
        </svg>
        <span>0412 358 971</span>
      </li>
      <li class="contact-item">
        <svg class="contact-icon" viewBox="0 0 24 24" aria-hidden="true">
          <path d="M12 1a7.5 7.5 0 0 0-7.5 7.5C4.5 14 12 23 12 23s7.5-9 7.5-14.5A7.5 7.5 0 0 0 12 1zm0 10.5a3 3 0 1 1 0-6 3 3 0 0 1 0 6z"/>
        </svg>
        <span>ABN 37 814 529 106</span>
      </li>
      <li class="contact-item">
        <svg class="contact-icon" viewBox="0 0 24 24" aria-hidden="true">
          <path d="M12 2 1 12h3v10h6v-6h4v6h6V12h3z"/>
        </svg>
        <span>PO Box 418 KELWOOD NSW 2619</span>
      </li>
      <li class="contact-item">
        <svg class="contact-icon" viewBox="0 0 24 24" aria-hidden="true">
          <path d="M2 5h20v14H2z M2 5l10 8 10-8" fill="none" stroke="#9ccb3b" stroke-width="2"/>
          <path d="M2 5h20l-10 8z"/>
        </svg>
        <span>l.pettigrew@corvanmail.net</span>
      </li>
    </ul>
  </article>
</body>
</html>
```